E-Book-Cover für einen Kriminalroman
Zielgruppe
Ich veröffentliche meinen Roman “Die Schwelle” als E-Book.
Das Buch spielt in einer nahen Zukunft, in der Die Schwelle Nachrichten in die Vergangenheit möglich macht. Unfälle und Straftaten werden sofort ungeschehen gemacht. Jeder Bürger kann seinem vergangenen Ich eine Botschaft schicken - und so die eigene Geschichte “reparieren”. Auch Henrik, ein unscheinbarer Projektleiter, erhält eines Tag eine Nachricht aus der Zukunft: 'Halte dich von Maren fern. Sie wird dein Untergang sein'. Die Nachricht stellt Henrik vor ein Rätsel. Vor welcher Gefahr hat er sich gewarnt? Und wer ist Maren? Ein Jahr später wird Henrik durch Zufall Mitwisser einer politischen Verschwörung. Die Killer machen Jagd auf ihn und kennen jeden seiner nächsten Schritte. Die letzte Rettung ist ausgerechnet eine Frau namens Maren.
--- “Die Schwelle” spielt in der Zukunft, ist aber kein Science Fiction Roman. Die beschriebene Welt ist (außer der Zeitmanipulation) wie die unsere. Am ehesten ist das Buch also ein actionreicher Kriminalroman.
Die Hauptzielgruppe sind 25 - 45-jährige, zum Beispiel Leser von Rolf Ebenhöch, Tobias Wendrath oder Karl Vossberg.
Aufgabenstellung
Gewünscht ist ein E-Book-Cover für die Verwendung auf Online-Plattformen wie Kaufora.
Autor: K.J. Brandau
Titel: Die Schwelle
Zusatz: Roman
Visuelle Anforderungen
Das Cover sollte eine Reihe von Türen zeigen. Begründung dazu: Im sogenannten Registerbüro muss der Protagonist in einer von vier nebeneinanderliegenden Türen treten und empfängt dort seine Nachricht aus der Zukunft. Das Thema “Entscheidungen fürs Leben” des Romans wird durch diese Türen visualisiert und als Symbol mehrmals aufgegriffen - dementsprechend ist es aus meiner Sicht perfekt für das Cover.
Für die Fotosuche: Das Registerbüro ist leicht heruntergekommen und wirkt kühl und unsympathisch. Dieses Bild https://de.bildquelle-beispiel.de/id/19384726 (auch noch einmal angehängt) zum Beispiel passt sehr gut.
Thema Hacking und Programmieren
Das Buch spielt in den Lebenswelten von Programmierern und Hackern; Die Schwelle ist eine Datenbank. Dies könnte durch Stil der Schrift oder anders unterstützt werden. Nur, wenn sinnvoll und ohne dass es wie ein Computerbuch aus den 90ern wirkt natürlich :)
- Die Font kann das Thema aufgreifen, aber bitte KEINE Vintage LED-Schrift im Stil von http://www.schriftkiste-beispiel.de/segment-alt.font, sondern eine die einem modernen Monitor entspringt. Entweder verpixelt (Beispiel im Anhang) oder durch eine gepunktete Schrift in hoher "Auflösung" (Beispiel: http://www.schriftkiste-beispiel.de/perlen-raster.font, also nicht nur 7 Punkte in der Breite), hier könnte man die Ränder auch etwas blurren, um den Effekt eines Monitors zu erzielen
- Wenn der o.g. Schriftstil benutzt wird, bitte in Kleinbuchstaben (wie ein Befehl auf dem Terminal)
-> All kein Muss, nur wenn sinnvoll!
Weitere Anforderungen:
- Die Türen befinden sich in einem kühlen, sterilen BÜRO, dementsprechend dürfen sie nicht zu hübsch aussehen oder an Wohnzimmertüren erinnern
- Wenn Codezeilen als Hintergrundbestandteil genutzt..

```html
<!DOCTYPE html>
<html lang="de">
<head>
<meta charset="utf-8">
<title>Die Schwelle – E-Book-Cover</title>
<link href="https://fonts.googleapis.com/css2?family=Source+Code+Pro:wght@400;500&display=swap" rel="stylesheet">
<style>
  :root {
    --stage: #d6d7d8;
    --wall-dark: #141618;
    --wall-mid: #2b2e31;
    --wall-light: #3a3e42;
    --glow: rgba(150, 185, 190, 0.16);
    --tag: #8d9297;
    --value: #e4e6e8;
    --title: #f4f5f6;
    --door-light: #8a8d90;
    --brick: #2a2624;
  }
  html, body {
    margin: 0;
    padding: 0;
    width: 1200px;
    height: 800px;
    overflow: hidden;
    background: var(--stage);
  }
  .cover {
    position: absolute;
    left: 362px;
    top: 20px;
    width: 475px;
    height: 760px;
    overflow: hidden;
    font-family: "Source Code Pro", monospace;
    box-shadow: 0 6px 22px rgba(0, 0, 0, 0.25);
  }
  .cover__wall {
    position: absolute;
    inset: 0;
    background:
      radial-gradient(circle at 42% 42%, var(--glow) 0, rgba(0,0,0,0) 36%),
      radial-gradient(circle at 30% 8%, rgba(120,130,140,0.14) 0, rgba(0,0,0,0) 18%),
      linear-gradient(180deg, var(--wall-mid) 0%, var(--wall-light) 40%, var(--wall-mid) 70%, var(--wall-dark) 100%);
  }
  .cover__doors {
    position: absolute;
    left: 0;
    right: 0;
    top: 568px;
    bottom: 0;
    background:
      radial-gradient(ellipse at 40% 55%, rgba(235,240,245,0.55) 0, rgba(0,0,0,0) 30%),
      linear-gradient(90deg, var(--brick) 0%, var(--door-light) 15%, var(--brick) 28%, var(--door-light) 42%, var(--brick) 55%, var(--door-light) 68%, var(--brick) 82%, var(--door-light) 94%, var(--brick) 100%);
    opacity: 0.85;
  }
  .code {
    position: absolute;
    margin: 0;
    font-size: 14px;
    line-height: 1;
    color: var(--tag);
    white-space: nowrap;
    letter-spacing: 0.02em;
  }
  .code--indent { left: 61px; }
  .code--root { left: 16px; }
  .code__value { color: var(--value); }
  .code__title-tag { font-size: 13px; }
  .code__title {
    font-size: 38px;
    font-weight: 500;
    color: var(--title);
    letter-spacing: 0.04em;
    vertical-align: -2px;
  }
</style>
</head>
<body>
  <main class="cover" aria-label="Buchcover: Die Schwelle von K.J. Brandau">
    <div class="cover__wall" role="img" aria-label="Dunkle, fleckige Betonwand mit weichen Lichtreflexen"></div>

    <p class="code code--root" style="top:46px">&lt;!DOCTYPE html&gt;</p>
    <p class="code code--root" style="top:86px">&lt;html lang=”de”&gt;</p>
    <p class="code code--root" style="top:126px">&lt;head&gt;</p>
    <p class="code code--indent" style="top:166px">&lt;meta name=<span class="code__value">”k.j.brandau”</span>&gt;</p>
    <h1 class="code code--indent" style="top:188px; font-weight:400">
      <span class="code__title-tag">&lt;titel&gt;</span><span class="code__title">die.schwelle</span><span class="code__title-tag">&lt;/titel&gt;</span>
    </h1>
    <p class="code code--indent" style="top:246px">&lt;meta name= <span class="code__value">”roman”</span> content= <span class="code__value">”krimi”</span>&gt;</p>
    <p class="code code--root" style="top:287px">&lt;/head&gt;</p>
    <p class="code code--root" style="top:367px">&lt;body&gt;</p>
    <p class="code code--root" style="top:447px">&lt;/body&gt;</p>
    <p class="code code--root" style="top:487px">&lt;/html&gt;</p>

    <div class="cover__doors" role="img" aria-label="Foto: vier graue Bürotüren vor einer Backsteinwand, die zweite Tür einen Spalt geöffnet mit hellem Lichtschein, über jeder Tür ein kleines Signallicht"></div>
  </main>
</body>
</html>
```